Business Cards for IT Consulting Company (Managed Service Provider)

I am looking to have some business cards printed and would like some designs. We are an IT Consulting company based in Vancouver BC. I would like a nice clean and modern look to the cards. I have uploaded all the versions of my logo so parts can be used as needed. Here is a snippit from our website homepage:

Quillbrook Networks Ltd. is an IT Solutions Partner located in Vancouver BC, Canada. We offer IT solutions and support to customers in the greater Vancouver Area. With expertise in Microsoft platforms, as well as Linux and Mac OSX and over 12 years experience in the IT industry, Quillbrook Networks is dedicated to offering our clients top quality service and products. We take pride in the solutions we offer our customers. The greatest compliment a client can give us is to recommend our services.

Quillbrook Networks Ltd. offers a wide range of IT services from onsite service to remote support and managed service solutions. This allows clients to choose the support path that best suits their company’s needs. Supporting many different sized companies from small to enterprise level over the past 12 years Quillbrook Networks has the experience and expertise needed to ensure things run smoothly. Allowing our clients to focus on doing business.

Revolutionizing the way IT services are delivered.

Quillbrook Networks is dedicated to providing our clients with IT solutions that work and grow with them for years to come. This philosophy helps save money in the long run instead of replacing equipment constantly. Far too often IT solutions are not well thought out and while possibly solving the problem at hand, require replacement due to growth or quality within a very short time frame. Quillbrook Networks takes pride in providing solutions that will last and be able to accommodate growth without the need for replacement.

Industry/Entity Type

Information Technology

Contact Information for Business Card

Quillbrook Networks Ltd.
(Employee Name)
Eml: (Employees Email Address)
Web: quillbrook.me
Ph: 604-555-0148

Font styles to use
Serif
Sans Serif

Requirements
Must have
• The Company logo and company colors.
Nice to have
• - Our tag line: "Revolutionizing IT Services" or "Revolutionizing the way IT services are delivered."
• - Also I really like the idea of nature and technology together blending which is sort of where my logo came from so integrating that somehow onto the business cards would be great.

```html
<!DOCTYPE html>
<html lang="en">
<head>
<meta charset="utf-8">
<title>Quillbrook Networks Ltd. – Business Cards</title>
<link rel="stylesheet" href="https://fonts.googleapis.com/css2?family=Source+Sans+3:ital,wght@0,400;0,600;1,600&display=swap">
<style>
  :root {
    --brand-blue: #00aeef;
    --ink-grey: #4a4a4a;
    --card-white: #ffffff;
    --backdrop: #ebe9e6;
    --font-main: "Source Sans 3", Arial, sans-serif;
  }
  * { box-sizing: border-box; margin: 0; padding: 0; }
  html, body {
    width: 1200px; height: 900px; overflow: hidden;
    background: var(--backdrop);
    font-family: var(--font-main);
  }
  .canvas { position: relative; width: 1200px; height: 900px; }

  .card {
    position: absolute;
    border-radius: 18px;
    overflow: hidden;
    box-shadow: 0 6px 20px rgba(0,0,0,0.15);
  }

  /* Front card */
  .card--front {
    left: 78px; top: 34px; width: 588px; height: 364px;
    background: var(--card-white);
  }
  .card--front .brand-band {
    position: absolute; left: 0; right: 0; top: 29px; height: 99px;
    background: var(--brand-blue);
  }
  .card--front .brand-pill {
    position: absolute; left: 109px; top: 29px; width: 365px; height: 99px;
    background: var(--card-white);
    border-radius: 50px;
    display: flex; align-items: center; justify-content: center;
  }
  .brand-name {
    font-weight: 600; font-size: 26px; letter-spacing: 0.2px; white-space: nowrap;
  }
  .card--front .brand-name { color: var(--brand-blue); }

  .holder-name {
    position: absolute; left: 0; right: 0; top: 198px;
    text-align: center; font-size: 21px; font-weight: 600; color: var(--ink-grey);
  }
  .holder-name .first { color: var(--brand-blue); }

  .contact-list {
    position: absolute; left: 0; right: 0; top: 251px;
    list-style: none; text-align: center;
    font-size: 15.5px; line-height: 24.5px; color: var(--ink-grey);
  }
  .contact-list .label { color: var(--brand-blue); font-weight: 600; }

  /* Back card */
  .card--back {
    left: 389px; top: 505px; width: 566px; height: 351px;
    background: var(--brand-blue);
  }
  .card--back .brand-band {
    position: absolute; left: 0; right: 0; top: 82px; height: 96px;
    background: var(--card-white);
  }
  .card--back .brand-pill {
    position: absolute; left: 121px; top: 82px; width: 339px; height: 96px;
    background: var(--brand-blue);
    border-radius: 48px;
    display: flex; align-items: center; justify-content: center;
  }
  .card--back .brand-name { color: var(--card-white); font-size: 24px; }

  .tagline {
    position: absolute; left: 0; right: 0; top: 288px;
    text-align: center; color: var(--card-white);
    font-style: italic; font-weight: 600; font-size: 19px;
  }
</style>
</head>
<body>
<main class="canvas">
  <section class="card card--front" aria-label="Business card front">
    <div class="brand-band"></div>
    <div class="brand-pill"><span class="brand-name">Quillbrook Networks Ltd.</span></div>
    <h1 class="holder-name"><span class="first">Daniel</span> Hartley</h1>
    <ul class="contact-list">
      <li><span class="label">T:</span> 604-555-0148</li>
      <li><span class="label">E:</span> info@quillbrook.me</li>
      <li><span class="label">W:</span> www.quillbrook.me</li>
    </ul>
  </section>

  <section class="card card--back" aria-label="Business card back">
    <div class="brand-band"></div>
    <div class="brand-pill"><span class="brand-name">Quillbrook Networks Ltd.</span></div>
    <p class="tagline">Revolutionizing IT Services</p>
  </section>
</main>
</body>
</html>
```